Varentoria Business Card and Letter Head

We are a leadership assessment consultancy based in Sydney, Australia. We help executive-level decison-makers select leaders for more senior level roles in corporate and government organisations. Our methodology is based on the latest research from the field of neuroscience.
We need a business card design and matching letter head that presents our company, Varentoria, as a:
1. trusted adviser to senior executive-level decison makers
2. niche consultancy who are experts in the field of assessing leadership talent
3. results-focused solution provider who balance scientific methods with pragmatic solutions
The following company details should be used in all designs:
Company Name: Varentoria
Details (for business card):
Derek Hanford
Prime Capacity Officer
Level 29, Marlow Tower
7 Marlow Square
Sydney, NSW 2000 Australia
Phone: 1300 582 714
Mobile: 0412 637 258
Email: derek.hanford@varentoria-example.com.au
Website: varentoria-example.com.au
I have attached the logo for Varentoria (for both a white and black background) - your business card and letter head designs must incoporate this logo and colour scheme.
Thanks for your interest in this project, I'm looking forward to receiving your ideas.
Regards,
Derek
Target Market(s)
Executive-level decison-makers in corporate and government organisations (e.g., CEO, VP, Head of Human Resources)
Industry/Entity Type
Leadership
Look and feel

```html
<!DOCTYPE html>
<html lang="en">
<head>
<meta charset="utf-8">
<title>Varentoria Business Cards</title>
<link href="https://fonts.googleapis.com/css2?family=Source+Sans+3:wght@400;600;700&display=swap" rel="stylesheet">
<style>
  :root {
    --brand-red: #c0311f;
    --ink-dark: #3d3d3f;
    --ink-body: #333333;
    --divider: #b8b8b8;
    --card-white: #ffffff;
    --stage: #e9e7e4;
  }
  html, body {
    margin: 0;
    padding: 0;
    width: 1200px;
    height: 741px;
    overflow: hidden;
    background: var(--stage);
    font-family: "Source Sans 3", "Myriad Pro", Arial, sans-serif;
  }
  .sheet {
    position: relative;
    width: 1200px;
    height: 741px;
  }
  .card {
    position: absolute;
    width: 493px;
    height: 281px;
    background: var(--card-white);
    box-shadow: 0 2px 6px rgba(0,0,0,0.18);
    box-sizing: border-box;
  }
  .card--front-light { left: 38px;  top: 66px; }
  .card--front-dark  { left: 672px; top: 66px; }
  .card--back-light  { left: 27px;  top: 393px; }
  .card--back-dark   { left: 680px; top: 393px; }

  .holder {
    position: absolute;
    top: 26px;
    left: 0;
    width: 100%;
    text-align: center;
    font-size: 13px;
    color: var(--ink-body);
  }
  .holder__name {
    color: var(--brand-red);
    font-weight: 700;
    font-size: 16px;
  }
  .wordmark {
    position: absolute;
    left: 0;
    width: 100%;
    display: flex;
    justify-content: center;
    align-items: center;
    gap: 14px;
  }
  .card--front-light .wordmark,
  .card--front-dark .wordmark { top: 82px; }
  .card--back-light .wordmark,
  .card--back-dark .wordmark { top: 100px; }
  .wordmark__square {
    width: 22px;
    height: 22px;
    background: var(--brand-red);
  }
  .wordmark__name {
    font-weight: 700;
    font-size: 50px;
    line-height: 1;
    color: var(--ink-dark);
    letter-spacing: -0.5px;
  }
  .address {
    position: absolute;
    top: 195px;
    left: 0;
    width: 100%;
    text-align: center;
    font-size: 12px;
    color: var(--brand-red);
  }
  .contacts {
    position: absolute;
    top: 226px;
    left: 0;
    width: 100%;
    display: flex;
    justify-content: center;
    font-size: 11px;
    color: var(--ink-body);
  }
  .contacts__group {
    display: flex;
    flex-direction: column;
    gap: 3px;
    padding: 0 10px;
  }
  .contacts__group--phones {
    border-left: 1px solid var(--divider);
  }
  .contact {
    display: flex;
    align-items: center;
    gap: 6px;
    line-height: 13px;
  }
  .contact svg { width: 10px; height: 10px; flex: none; }
  .site {
    position: absolute;
    top: 255px;
    left: 0;
    width: 100%;
    text-align: center;
    font-size: 16px;
    letter-spacing: 1.2px;
    color: var(--ink-body);
  }
</style>
</head>
<body>
<main class="sheet">

  <section class="card card--front-light" aria-label="Business card front, light version">
    <p class="holder" style="margin:0"><span class="holder__name">Derek Hanford,</span> Prime Capacity Officer</p>
    <div class="wordmark"><span class="wordmark__square"></span><span class="wordmark__name">Varentoria</span></div>
    <p class="address" style="margin:0">Level 29, Marlow Tower 7 Marlow Square Sydney, NSW 2000 Australia</p>
    <div class="contacts">
      <div class="contacts__group">
        <span class="contact"><svg viewBox="0 0 10 10"><rect x="0" y="2" width="10" height="7" fill="#c0311f"/><path d="M0 2 L5 6 L10 2" stroke="#fff" fill="none"/></svg>derek.hanford@varentoria-example.com.au</span>
        <span class="contact"><svg viewBox="0 0 10 10"><circle cx="5" cy="5" r="5" fill="#c0311f"/><path d="M0 5 H10 M5 0 V10" stroke="#fff" stroke-width="0.8"/></svg>www.varentoria-example.com.au</span>
      </div>
      <div class="contacts__group contacts__group--phones">
        <span class="contact"><svg viewBox="0 0 10 10"><path d="M2 1 L4 3 L3 4 Q4 6 6 7 L7 6 L9 8 L8 9.5 Q2 9 0.5 2 Z" fill="#c0311f"/></svg>1300 582 714</span>
        <span class="contact"><svg viewBox="0 0 10 10"><rect x="3" y="0" width="5" height="10" rx="1" fill="#c0311f"/><rect x="4" y="1.5" width="3" height="4" fill="#fff"/></svg>0412 637 258</span>
      </div>
    </div>
  </section>

  <section class="card card--front-dark" aria-label="Business card front, dark version">
    <p class="holder" style="margin:0"><span class="holder__name">Derek Hanford,</span> Prime Capacity Officer</p>
    <div class="wordmark"><span class="wordmark__square"></span><span class="wordmark__name">Varentoria</span></div>
    <p class="address" style="margin:0">Level 29, Marlow Tower 7 Marlow Square Sydney, NSW 2000 Australia</p>
    <div class="contacts">
      <div class="contacts__group">
        <span class="contact"><svg viewBox="0 0 10 10"><rect x="0" y="2" width="10" height="7" fill="#c0311f"/><path d="M0 2 L5 6 L10 2" stroke="#fff" fill="none"/></svg>derek.hanford@varentoria-example.com.au</span>
        <span class="contact"><svg viewBox="0 0 10 10"><circle cx="5" cy="5" r="5" fill="#c0311f"/><path d="M0 5 H10 M5 0 V10" stroke="#fff" stroke-width="0.8"/></svg>www.varentoria-example.com.au</span>
      </div>
      <div class="contacts__group contacts__group--phones">
        <span class="contact"><svg viewBox="0 0 10 10"><path d="M2 1 L4 3 L3 4 Q4 6 6 7 L7 6 L9 8 L8 9.5 Q2 9 0.5 2 Z" fill="#c0311f"/></svg>1300 582 714</span>
        <span class="contact"><svg viewBox="0 0 10 10"><rect x="3" y="0" width="5" height="10" rx="1" fill="#c0311f"/><rect x="4" y="1.5" width="3" height="4" fill="#fff"/></svg>0412 637 258</span>
      </div>
    </div>
  </section>

  <section class="card card--back-light" aria-label="Business card back, light version">
    <div class="wordmark"><span class="wordmark__square"></span><span class="wordmark__name">Varentoria</span></div>
    <p class="site" style="margin:0">www.varentoria-example.com.au</p>
  </section>

  <section class="card card--back-dark" aria-label="Business card back, dark version">
    <div class="wordmark"><span class="wordmark__square"></span><span class="wordmark__name">Varentoria</span></div>
    <p class="site" style="margin:0">www.varentoria-example.com.au</p>
  </section>

</main>
</body>
</html>
```